One of a Kind Clean Business Card

We need to design a new business card template for our company. Our company designs and produced merchandising displays. You can see a sample of what we produce on our site www.qorvanexhibits.net. I have uploaded our logo in vector format, as well as a picture of our current business cards. We want a totally different look. We want simple and clean, looking forward to seeing what people create.
Updates

I would like to update the address for Qorvan Display Group Inc. 518 E Tollmere Ln Arlington Heights, IL 60017 Would also note. No QR codes

Industry/Entity Type

Business

Contact Information for Business Card

Need a 1 sided business card designed.

Font styles to use
Serif

Requirements
Must have
• Easy to view; Clean Design
Nice to have
• Features that promote engineering and creativity
Should not have
• Too much clutter, keep it simple

```html
<!DOCTYPE html>
<html lang="en">
<head>
<meta charset="utf-8">
<title>Qorvan Display Group Inc. – Business Card</title>
<link href="https://fonts.googleapis.com/css2?family=Lora:wght@400;600&display=swap" rel="stylesheet">
<style>
  :root {
    --backdrop: #e9e6e1;
    --card: #0a0a0a;
    --card-sheen: #222222;
    --ink: #f2f2f2;
    --accent: #b0283a;
  }
  * { margin: 0; padding: 0; box-sizing: border-box; }
  html, body {
    width: 1200px; height: 1022px; overflow: hidden;
    background: var(--backdrop);
    font-family: "Lora", Georgia, "Times New Roman", serif;
  }
  .stage {
    width: 1200px; height: 1022px;
    display: flex; align-items: center; justify-content: center;
  }
  .business-card {
    position: relative;
    width: 1000px; height: 572px;
    overflow: hidden;
    background: linear-gradient(155deg, var(--card-sheen) 0%, var(--card) 40%, var(--card) 100%);
    color: var(--ink);
    box-shadow: 0 14px 40px rgba(0,0,0,.25);
  }
  .brand {
    position: absolute; left: 80px; top: 70px;
    display: flex; align-items: flex-end; gap: 18px;
    padding: 0 24px 14px 0;
    border-bottom: 2px solid var(--ink);
  }
  .brand-mark {
    width: 64px; height: 64px; flex: none;
    border: 2px solid var(--ink);
  }
  .brand-name {
    font-weight: 400; font-size: 34px; line-height: 1;
    letter-spacing: 1.5px; text-transform: uppercase;
    color: var(--accent);
  }
  .person-name {
    position: absolute; left: 80px; top: 210px;
    font-weight: 600; font-size: 36px; line-height: 1.2;
  }
  .name-rule {
    position: absolute; left: 80px; right: 0; top: 266px;
    height: 2px; background: var(--accent);
  }
  .contact-list {
    position: absolute; left: 80px; top: 292px;
    list-style: none;
  }
  .contact-item {
    display: flex; align-items: center; gap: 16px;
    height: 46px;
    font-weight: 400; font-size: 24px; letter-spacing: .3px;
  }
  .contact-icon { width: 22px; height: 22px; flex: none; }
  .icon-fill { fill: var(--accent); }
  .icon-line { fill: none; stroke: var(--accent); stroke-width: 1.8; }
  .icon-cut { fill: none; stroke: var(--card); stroke-width: 1.4; }
  .address { margin-top: 6px; }
</style>
</head>
<body>
<main class="stage">
  <article class="business-card">
    <header class="brand">
      <span class="brand-mark" aria-hidden="true"></span>
      <span class="brand-name">Qorvan Display Group Inc.</span>
    </header>

    <h1 class="person-name">Dana Reuter</h1>
    <div class="name-rule"></div>

    <ul class="contact-list">
      <li class="contact-item">
        <svg class="contact-icon" viewBox="0 0 20 20" aria-hidden="true">
          <path class="icon-fill" d="M5 2l3 4-2 2c1 2.5 3.5 5 6 6l2-2 4 3-2 3C9 18 2 11 2 4z"/>
        </svg>
        <span>815-555-0142</span>
      </li>
      <li class="contact-item">
        <svg class="contact-icon" viewBox="0 0 20 20" aria-hidden="true">
          <rect class="icon-line" x="5" y="1.5" width="10" height="17" rx="1.5"/>
        </svg>
        <span>312-555-0178</span>
      </li>
      <li class="contact-item">
        <svg class="contact-icon" viewBox="0 0 20 20" aria-hidden="true">
          <rect class="icon-fill" x="1" y="4" width="18" height="12"/>
          <path class="icon-cut" d="M1.5 4.5L10 11l8.5-6.5"/>
        </svg>
        <span>dreuter@qorvanexhibits.net</span>
      </li>
      <li class="contact-item">
        <svg class="contact-icon" viewBox="0 0 20 20" aria-hidden="true">
          <circle class="icon-line" cx="10" cy="10" r="8"/>
          <ellipse class="icon-line" cx="10" cy="10" rx="3.5" ry="8"/>
          <path class="icon-line" d="M2 10h16M3.5 6h13M3.5 14h13"/>
        </svg>
        <span>www.qorvanexhibits.net</span>
      </li>
      <li class="contact-item address">
        <span>518 E Tollmere Ln Arlington Heights, IL 60017</span>
      </li>
    </ul>
  </article>
</main>
</body>
</html>
```